Honey Company from Florida Needs Sweet and Buzz-worthy Site

Website Requests:
-Deluxe 5-Page Website with SSL-Secure Online Store (Shopify)
-High-end imagery to appeal to a discerning consumer
-Detailed verbiage with strong SEO and easy readability
-Design principles: simple, chic, luxe, earthy
Pages:
1. Home {Local, Raw American Honey from Florida}
2. The Hive
> About Us
>Meet the Beekeepers
3. Buy Honey
> Shopify retail store
4. The Buzz {News, Recipes & More}
> Blog
5. Contact Us {We're Buzzin' to Meet You}
> Store Hours
> Phone Number
> Address
> Quick Contact Form
Attachments: Web design notes, Logo, Color Codes, Inspiration Photos
Target Market(s)
High-end honey consumer in the U.S.
Industry/Entity Type
Upscale honey enthusiasts; direct to consumer sales.
Coding
Coded - Design and coding required
Number of Pages Required
5+ page
Requirements
Must have
- Upscale look and feel, easy usability for quick sales.

```html
<!DOCTYPE html>
<html lang="en">
<head>
<meta charset="utf-8">
<title>Goldcomb Honey Co — Raw Florida Honey</title>
<link rel="stylesheet" href="https://fonts.googleapis.com/css2?family=Bebas+Neue&family=Poppins:wght@300;400;500&display=swap">
<style>
:root{
  --honey:#e8bf3e;
  --honey-deep:#b86a14;
  --ink:#1f1f1f;
  --text:#555;
  --paper:#ffffff;
  --cream:#fff6d6;
  --night:#262321;
  --line:#d6d6d6;
}
*{box-sizing:border-box;margin:0;padding:0}
html,body{width:1200px;height:3542px;overflow:hidden}
body{position:relative;background:var(--paper);font-family:'Poppins',sans-serif;color:var(--text)}
.abs{position:absolute}
.display{font-family:'Bebas Neue',sans-serif;color:var(--ink);font-weight:400;letter-spacing:.5px}
.btn{position:absolute;display:flex;align-items:center;justify-content:center;font-family:'Bebas Neue',sans-serif;font-size:20px;letter-spacing:.5px;color:var(--ink);text-decoration:none}
.btn-solid{background:var(--honey)}
.btn-outline{border:2px solid var(--ink);background:transparent}
.accent{position:absolute;height:4px;width:69px;background:linear-gradient(90deg,var(--ink) 0 55%,var(--honey) 55%)}
.copy p{font-size:12.5px;line-height:24px;margin-bottom:16px;color:var(--text)}

/* hero */
.hero{left:0;top:0;width:1200px;height:685px;background:linear-gradient(90deg,#3b2a1e 0%,#5b4331 35%,#6e5238 55%,#7a4a1a 75%,#a45a14 88%,#5b3a22 100%)}
.hero-jar{left:600px;top:0;width:600px;height:685px;background:radial-gradient(ellipse at 60% 55%,#c4661a 0%,#8a3f10 40%,rgba(80,50,30,0) 75%)}
.menu{left:110px;top:60px}
.brand{left:557px;top:22px;width:108px;height:108px;display:flex;flex-direction:column;align-items:center;justify-content:center;border:2px solid #fff;border-radius:50%;color:#fff;font-family:'Bebas Neue',sans-serif;font-size:22px;line-height:22px;text-align:center}
.brand small{font-size:12px;letter-spacing:2px}
.cart{left:1056px;top:56px}
.hero-title{left:108px;top:206px;width:670px;font-size:58px;line-height:66px;color:#fff}

/* split rows */
.photo{position:absolute}
.honeycomb{position:absolute;background:linear-gradient(120deg,var(--cream) 0%,#fffdf5 45%,#fff9e3 100%)}
.heading{position:absolute;font-size:46px;line-height:50px}

/* video */
.video{left:0;top:1212px;width:1200px;height:514px;background:linear-gradient(180deg,#1d2f4c 0%,#2b4160 40%,#2d3f2a 72%,#1c2418 100%)}
.play{left:568px;top:1437px}

/* cta band */
.cta{left:0;top:2781px;width:1200px;height:412px;background:var(--night)}
.cta-bottles{left:160px;top:2781px;width:880px;height:412px;background:linear-gradient(90deg,rgba(0,0,0,0) 0%,rgba(70,45,20,.45) 20%,rgba(0,0,0,0) 40%,rgba(70,45,20,.45) 50%,rgba(0,0,0,0) 60%,rgba(70,45,20,.45) 80%,rgba(0,0,0,0) 100%)}
.cta-line{left:565px;top:2868px;width:70px;height:3px;background:#fff}
.cta-title{left:0;top:2880px;width:1200px;text-align:center;color:#fff;font-size:52px;line-height:56px}
.cta-text{left:200px;top:2950px;width:800px;text-align:center;color:#eee;font-size:13px;line-height:29px}

/* footer */
.footer{left:0;top:3193px;width:1200px;height:349px;background:linear-gradient(180deg,#ffffff 0%,#fdfbf4 100%)}
.foot-nav{left:110px;top:3263px;list-style:none}
.foot-nav li{font-size:15.5px;line-height:35px;color:var(--ink)}
.foot-contact{left:272px;top:3263px;font-size:15px;line-height:35px;color:var(--ink)}
.social{display:flex;gap:12px;margin-top:8px}
.social span{width:12px;height:12px;border-radius:50%;background:var(--ink);display:block}
.signup{left:650px;top:3262px;width:425px}
.signup h3{font-weight:400;font-size:18px;color:var(--ink);letter-spacing:.3px}
.signup p{font-size:14.5px;color:var(--ink);margin-top:4px}
.email{margin-top:34px;border-bottom:1px solid #999;padding-bottom:10px;display:flex;justify-content:space-between;font-size:12.5px;color:var(--ink)}
.email b{font-weight:500;font-size:12px;letter-spacing:.5px}
.copyright{left:0;top:3476px;width:1200px;text-align:center;font-size:13px;color:var(--ink)}
</style>
</head>
<body>

<!-- Hero -->
<section class="abs hero" role="img" aria-label="Photo of honey dripping from a wooden dipper into a glass jar on a rustic table"></section>
<div class="abs hero-jar" aria-hidden="true"></div>
<svg class="abs menu" width="26" height="20" viewBox="0 0 26 20" aria-label="Menu"><g stroke="#fff" stroke-width="2"><line x1="0" y1="2" x2="26" y2="2"/><line x1="0" y1="10" x2="26" y2="10"/><line x1="0" y1="18" x2="26" y2="18"/></g></svg>
<div class="abs brand">Goldcomb<small>Honey Co</small></div>
<svg class="abs cart" width="32" height="28" viewBox="0 0 32 28" aria-label="Cart"><g fill="none" stroke="#fff" stroke-width="2"><path d="M1 2h5l4 16h17l3-12H8"/><circle cx="12" cy="24" r="2"/><circle cx="25" cy="24" r="2"/></g></svg>
<h1 class="abs display hero-title">Blessed to bee-keep straight<br>from our beloved hives to<br>your lovely home</h1>
<a class="btn btn-solid" style="left:108px;top:418px;width:155px;height:51px">Watch Video</a>

<!-- About -->
<div class="photo" style="left:0;top:685px;width:600px;height:527px;background:linear-gradient(135deg,#3a3a3a 0%,#4a4a48 50%,#2f2f2f 100%)" role="img" aria-label="Photo of a gift-wrapped honey jar beside an open box with bees"></div>
<div class="honeycomb" style="left:600px;top:685px;width:600px;height:527px"></div>
<div class="photo" style="left:1070px;top:692px;width:130px;height:180px;background:radial-gradient(ellipse at 50% 35%,#f0a020 0%,#d4800e 45%,rgba(255,255,255,0) 72%)" role="img" aria-label="Illustration of a honey dipper dripping honey"></div>
<div class="accent" style="left:639px;top:727px"></div>
<h2 class="heading display" style="left:632px;top:750px">Goldcomb</h2>
<div class="abs copy" style="left:632px;top:810px;width:460px">
  <p>100% raw, unfiltered Florida honey straight from the beehives on his six-acre property, Goldcomb Honey Farm, 4812 Orchard Lane in Lakeview.</p>
  <p>Agricultural Company specializing in the Production of 100% Raw American Honey, and the Pollination of America's food crops.</p>
  <p>Our Honey comes straight from our beehives to your table. No filtering, heating, or any funny stuff. Just All Natural, 100% Pure Florida Honey</p>
  <p>Natural Wild Honey- flavors include Orange Blossom, Gallberry, Summer Wildflower, Winter Wildflower, and many more. Bee Pollen, Royal Jelly, and Bee venom. Bee removals are done by Marcus.</p>
</div>
<a class="btn btn-outline" style="left:634px;top:1120px;width:154px;height:51px">Read More</a>

<!-- Video -->
<section class="abs video" role="img" aria-label="Video still of a beekeeper in a hat lifting a honeycomb frame outdoors"></section>
<svg class="abs play" width="64" height="64" viewBox="0 0 64 64" aria-label="Play video"><circle cx="32" cy="32" r="30" fill="none" stroke="#fff" stroke-width="3"/><path d="M26 20l16 12-16 12z" fill="#fff"/></svg>

<!-- Importance of bees -->
<div class="honeycomb" style="left:0;top:1726px;width:600px;height:528px;background:linear-gradient(90deg,#fbe9a8 0%,#fff6d6 30%,#fff 70%)"></div>
<div class="accent" style="left:120px;top:1810px"></div>
<h2 class="heading display" style="left:111px;top:1834px">Importance of Bees</h2>
<div class="abs copy" style="left:111px;top:1893px;width:455px">
  <p>If the bee disappeared off the face of the Earth, man would have only four years left to live.</p>
  <p>Hyper-efficient insects do play a vital role in agriculture. Almonds, for example, are almost entirely dependent on honeybee pollination</p>
  <p>Over one-third of our entire diet is dependent on pollination from the honeybee. So, for every three bites of food you eat, you can thank the honeybee for one of those three bites</p>
</div>
<a class="btn btn-outline" style="left:111px;top:2118px;width:154px;height:51px">Read More</a>
<div class="photo" style="left:600px;top:1726px;width:600px;height:528px;background:linear-gradient(135deg,#e6e6e4 0%,#d9c7a4 30%,#7a5634 55%,#8a4a22 70%,#e4e4e2 100%)" role="img" aria-label="Photo of a wooden frame with honeycomb paper and a bottle of pure honey"></div>

<!-- Health benefits -->
<div class="photo" style="left:0;top:2254px;width:600px;height:527px;background:radial-gradient(ellipse at 40% 50%,#a8621e 0%,#c9a062 30%,#e2e2e0 65%,#e6e6e6 100%)" role="img" aria-label="Photo of stacked hexagonal honey jars in kraft packaging"></div>
<div class="accent" style="left:639px;top:2365px"></div>
<h2 class="heading display" style="left:632px;top:2388px">The Health Benefits of Honey</h2>
<div class="abs copy" style="left:632px;top:2450px;width:450px">
  <p>Raw honey is loaded with antioxidants to protect your body from cell damage due to free radicals. Honey has been long known as a folk remedy to help heal burns and wounds due to its antibacterial and antifungal properties. Honey is also very well known to soothe a sore throat. Try taking a spoonful of honey and add it to hot tea if you feel like you have a cold. Honey can also help as a cough suppressant.</p>
</div>
<a class="btn btn-outline" style="left:634px;top:2617px;width:154px;height:51px">Read More</a>

<!-- CTA band -->
<section class="abs cta"></section>
<div class="abs cta-bottles" role="img" aria-label="Dim photo of three honey bottles in a row"></div>
<div class="abs cta-line"></div>
<h2 class="abs display cta-title">Goldcomb</h2>
<p class="abs cta-text">Lorem ipsum dolor sit amet, consectetur adipiscing elit, sed do eiusmod tempor incididunt ut labore et dolore magna aliqua. Ut enim ad minim veniam, quis nostrud exercitation ullamco laboris nisi ut aliquip ex ea commodo consequat. Duis aute irure dolor in reprehenderit in voluptate velit esse</p>
<a class="btn btn-solid" style="left:522px;top:3060px;width:154px;height:48px">Contact Us</a>

<!-- Footer -->
<footer class="abs footer" role="img" aria-label="Faint illustrated background of bees and flowers"></footer>
<ul class="abs foot-nav">
  <li>Home</li><li>The Hive</li><li>Buy Honey</li><li>The Buzz</li><li>Contact</li>
</ul>
<div class="abs foot-contact">
  (555) 014-2270<br>4812 Orchard Lane,<br>Lakeview, FL 32000
  <div class="social" aria-label="Social links"><span></span><span></span></div>
</div>
<div class="abs signup">
  <h3>SIGN UP FOR UPDATES</h3>
  <p>Lorem ipsum dolor sit amet, consectetur adipiscing</p>
  <div class="email"><span>My email address</span><b>SUBSCRIBE &#9656;</b></div>
</div>
<div class="abs copyright">© 2021 All Rights Reserved</div>

</body>
</html>
```